Large online photo magazine needs redesign

We have previously digitised a historical photographic magazine of around 20,000 printed pages and made it available online. The magazine ran up to the early 1970s, and the content is largely black and white photographs of local events, accompanied by short captions.

Although the content is very rich, the design needs to be revisited so that:
* it is visually appealing
* it is responsive (i.e. works in browsers across all manner of devices)
* is faithful to the nature of the content

There are only a few core page types, and the central one is the article page, an example of which can be seen at:
http://snapgazette.example/gisborne/issue/KLR48_19600714/t1-body-d4.html

Any design submitted should be based on the treatment of an article page such as the above.

Given the large number of pages on our site, we need a design which can be templated to work for any content in the collection, i.e. we cannot hand-craft our templates to match a given page of content, rather a template must work acceptably well for all content.

The current site, although basic in design, has the advantage that it is quite efficient in the amount of data per page request (around 100k - 200k). While not adverse to web fonts, banner imagery etc, we will carefully consider the benefit gained from any such treatment against the amount of extra data that needs to be downloaded to the client's browser.

For the right design, we are able ourselves to adapt it to a CSS layout.

An example of each core page type is as follows (though for this project we only expect a design for a single page, as itemised above):

http://snapgazette.example/gisborne/index.html
http://snapgazette.example/gisborne/about.html
http://snapgazette.example/gisborne/help.html
http://snapgazette.example/gisborne/initial/index.html
http://snapgazette.example/gisborne/search/results?type=section&text=smith&cmdSubmit=Go
http://snapgazette.example/gisborne/advanced-search/index.html
http://snapgazette.example/gisborne/issue/KLR48_19600714/t1-front-d1.html
http://snapgazette.example/gisborne/issue/KLR48_19600714/index.html
http://snapgazette.example/gisborne/issue/KLR48_19600714/fig-KLR48_19600714_005a.html
http://snapgazette.example/gisborne/issue/KLR48_19600714/KLR48_19600714_012.html
http://snapgazette.example/gisborne/issue/KLR48_19600714/thumbnails.html

Target Market(s)

A general browsing audience of all ages, but skewed towards the older generations, and those interested in family / regional history.

The average user will not be particularly web-savy, and the treatment of the content should not detract / distract from the actual content itself.

Industry/Entity Type

Events

Requirements
Must have
• * it is visually appealing
The content should be visually appealing to the audience, which can be defined as a general browsing audience of all ages, but skewed towards the middle and older generations.

* it is responsive (the design can be adapted - by us - to work in browsers across all manner of devices)

The magazine covers (http://snapgazette.example/gisborne/issues/index.html) offer some possible inspiration for treatment of the material.

```html
<!DOCTYPE html>
<html lang="en">
<head>
<meta charset="utf-8">
<title>Browse Gisborne Snap Gazette</title>
<link href="https://fonts.googleapis.com/css2?family=Roboto:wght@400;500;700&display=swap" rel="stylesheet">
<style>
:root{
  --brand:#cc3b51;
  --brand-dark:#b52f44;
  --nav-top:#f4f4f4;
  --nav-bottom:#d9d9d9;
  --nav-line:#c9c9c9;
  --ink:#333333;
  --muted:#9a9a9a;
  --soft:#666666;
  --footer:#757575;
  --white:#ffffff;
  --rule:#c8c8c8;
}
*{box-sizing:border-box;margin:0;padding:0}
html,body{width:1064px;height:1200px;overflow:hidden;background:var(--white);font-family:"Roboto",Arial,sans-serif}
a{text-decoration:none;color:inherit}
.page{position:relative;width:1064px;height:1200px}
.masthead{height:88px;background:var(--brand);position:relative;color:var(--white)}
.brand-name{position:absolute;left:125px;top:30px;font-size:26px;font-weight:700;color:var(--white);letter-spacing:.5px}
.utility-links{position:absolute;right:126px;top:8px;font-size:11px;display:flex;gap:14px}
.utility-links .sep{opacity:.9}
.call{position:absolute;right:126px;top:48px;font-size:17px;display:flex;align-items:center;gap:6px}
.call svg{width:20px;height:20px}
.main-nav{height:44px;background:linear-gradient(var(--nav-top),var(--nav-bottom));border-bottom:2px solid var(--nav-line);position:relative}
.main-nav ul{list-style:none;display:flex;position:absolute;left:125px;top:0;height:42px}
.main-nav li{height:42px;display:flex;align-items:center;padding:0 30px;font-size:13.5px;color:var(--soft);border-right:1px solid var(--nav-line)}
.main-nav li:first-child{padding:0 30px 0 33px}
.search{position:absolute;right:120px;top:5px;display:flex;height:34px;border:1px solid #d5d5d5;background:var(--white)}
.search .field{width:154px;font-size:8.5px;color:var(--soft);padding:12px 9px;border-right:1px solid #d5d5d5}
.search .go{width:33px;font-size:10.5px;color:var(--muted);display:flex;align-items:center;justify-content:center}
.page-title{position:absolute;top:152px;width:100%;text-align:center;color:var(--brand);font-size:19.5px;font-weight:400}
.article{position:absolute;left:125px;width:812px;height:251px;border-bottom:1px dotted var(--rule)}
.article .photo{position:absolute;left:0;top:0;width:292px;height:216px}
.article .text{position:absolute;left:335px;top:3px;width:477px}
.article h2{font-size:17px;font-weight:400;color:var(--ink);margin-top:0}
.article p{font-size:11px;line-height:24px;color:var(--muted);margin-top:13px}
.meta{display:flex;align-items:center;gap:3px;margin-top:10px;font-size:9px;color:var(--soft)}
.meta .count{margin-right:2px;font-size:10px}
.meta svg{width:13px;height:13px}
.print{display:flex;align-items:center;gap:4px;margin-top:24px;font-size:11px;color:var(--brand)}
.print svg{width:12px;height:11px}
.pager{position:absolute;right:127px;top:1066px;font-size:10.5px;color:var(--brand);display:flex;gap:14px}
.site-footer{position:absolute;left:0;top:1104px;width:1064px;height:96px;background:var(--footer);color:var(--white)}
.footer-links{position:absolute;left:126px;top:28px;font-size:10px;display:flex;gap:8px}
.copyright{position:absolute;left:125px;top:57px;font-size:10px}
.licence{position:absolute;right:126px;top:12px;width:73px;height:26px;background:#222;border:1px solid #ddd;border-radius:2px}
.social{position:absolute;right:126px;top:51px;display:flex;gap:7px}
.social span{width:25px;height:25px;border-radius:50%;background:var(--white)}
</style>
</head>
<body>
<div class="page">
  <header class="masthead">
    <a class="brand-name" href="http://snapgazette.example/gisborne/index.html">Gisborne Snap Gazette</a>
    <nav class="utility-links">
      <a href="http://snapgazette.example/gisborne/advanced-search/index.html">Advanced search</a><span class="sep">|</span>
      <a href="http://snapgazette.example/gisborne/help.html">Help</a><span class="sep">|</span>
      <a href="#">Report an error</a>
    </nav>
    <div class="call">
      <svg viewBox="0 0 20 20"><circle cx="10" cy="10" r="10" fill="#fff"/><path d="M7 5.2c.6-.4 1.2-.2 1.5.4l.8 1.6c.2.5.1 1-.3 1.3l-.6.5c.5 1.2 1.4 2.2 2.6 2.7l.5-.6c.3-.4.9-.5 1.3-.3l1.6.8c.6.3.8 1 .4 1.5l-.6.9c-.5.6-1.3.9-2.1.6-2.8-1-4.9-3.1-5.9-5.9-.3-.8 0-1.6.6-2.1z" fill="#cc3b51"/></svg>
      <span>Call - 64 6 5550192</span>
    </div>
  </header>

  <nav class="main-nav">
    <ul>
      <li><a href="http://snapgazette.example/gisborne/index.html">Home</a></li>
      <li><a href="http://snapgazette.example/gisborne/about.html">About</a></li>
      <li><a href="http://snapgazette.example/gisborne/issues/index.html">Browse Gisborne Snap Gazette</a></li>
      <li><a href="http://snapgazette.example/gisborne/initial/index.html">A-Z people</a></li>
    </ul>
    <div class="search"><div class="field">Search Gisborne Snap Gazette</div><div class="go">GO</div></div>
  </nav>

  <h1 class="page-title">Browse Gisborne Snap Gazette</h1>

  <article class="article" style="top:219px">
    <div class="photo" role="img" aria-label="Black and white photograph of three smiling air hostess sisters in uniform caps" style="background:linear-gradient(135deg,#d8d2b8,#6e6a5c 45%,#2a2925 80%)"></div>
    <div class="text">
      <h2>Flying Sisters from Gisborne.....</h2>
      <p>This is probably something of a record--three sisters who are all air hostesses. They are the Harlow sisters.....Marguerite, Elsie, and Rosalind, daughters of Mr and Mrs T. R. Harlow.This is probably something of a record--three sisters who are all air hostesses. , and Rosalind, daughters of Mr and Mrs T. R. Harlow......</p>
      <div class="meta">
        <svg viewBox="0 0 13 13"><path d="M1.5 1.5h10v7h-6l-3 3v-3h-1z" fill="none" stroke="#cc3b51" stroke-width="1.3"/></svg><span class="count">0</span>
        <svg viewBox="0 0 13 13"><circle cx="6.5" cy="6.5" r="5.3" fill="none" stroke="#cc3b51" stroke-width="1.3"/><path d="M6.5 3.5v3.3l2 1.2" fill="none" stroke="#cc3b51" stroke-width="1.2"/></svg><span>November 3, 1960</span>
      </div>
      <a class="print" href="#"><svg viewBox="0 0 12 11"><rect x="3" y="0.5" width="6" height="3" fill="none" stroke="#999"/><rect x="0.5" y="3.5" width="11" height="4.5" rx="1" fill="#999"/><rect x="3" y="6.5" width="6" height="4" fill="#fff" stroke="#999"/></svg>Print This Article</a>
    </div>
  </article>

  <article class="article" style="top:504px">
    <div class="photo" role="img" aria-label="Black and white photograph of an air hostess smiling from an aircraft doorway" style="background:linear-gradient(160deg,#cfc8ad,#8a8470 40%,#22211e 75%)"></div>
    <div class="text">
      <h2>Flying Sisters from Gisborne.....</h2>
      <p>This is probably something of a record--three sisters who are all air hostesses. They are the Harlow sisters.....Marguerite, Elsie, and Rosalind, daughters of Mr and Mrs T. R. Harlow.This is probably something of a record--three sisters who are all air hostesses. , and Rosalind, daughters of Mr and Mrs T. R. Harlow......</p>
      <div class="meta">
        <svg viewBox="0 0 13 13"><path d="M1.5 1.5h10v7h-6l-3 3v-3h-1z" fill="none" stroke="#cc3b51" stroke-width="1.3"/></svg><span class="count">0</span>
        <svg viewBox="0 0 13 13"><circle cx="6.5" cy="6.5" r="5.3" fill="none" stroke="#cc3b51" stroke-width="1.3"/><path d="M6.5 3.5v3.3l2 1.2" fill="none" stroke="#cc3b51" stroke-width="1.2"/></svg><span>November 3, 1960</span>
      </div>
      <a class="print" href="#"><svg viewBox="0 0 12 11"><rect x="3" y="0.5" width="6" height="3" fill="none" stroke="#999"/><rect x="0.5" y="3.5" width="11" height="4.5" rx="1" fill="#999"/><rect x="3" y="6.5" width="6" height="4" fill="#fff" stroke="#999"/></svg>Print This Article</a>
    </div>
  </article>

  <article class="article" style="top:792px">
    <div class="photo" role="img" aria-label="Black and white photograph of an old truss bridge across a river with a printed caption" style="background:linear-gradient(180deg,#e4e0cc,#a9a590 45%,#5c5a4e 65%,#d6d1bb)"></div>
    <div class="text">
      <h2>Flying Sisters from Gisborne.....</h2>
      <p>This is probably something of a record--three sisters who are all air hostesses. They are the Harlow sisters.....Marguerite, Elsie, and Rosalind, daughters of Mr and Mrs T. R. Harlow.This is probably something of a record--three sisters who are all air hostesses. , and Rosalind, daughters of Mr and Mrs T. R. Harlow......</p>
      <div class="meta">
        <svg viewBox="0 0 13 13"><path d="M1.5 1.5h10v7h-6l-3 3v-3h-1z" fill="none" stroke="#cc3b51" stroke-width="1.3"/></svg><span class="count">0</span>
        <svg viewBox="0 0 13 13"><circle cx="6.5" cy="6.5" r="5.3" fill="none" stroke="#cc3b51" stroke-width="1.3"/><path d="M6.5 3.5v3.3l2 1.2" fill="none" stroke="#cc3b51" stroke-width="1.2"/></svg><span>November 3, 1960</span>
      </div>
      <a class="print" href="#"><svg viewBox="0 0 12 11"><rect x="3" y="0.5" width="6" height="3" fill="none" stroke="#999"/><rect x="0.5" y="3.5" width="11" height="4.5" rx="1" fill="#999"/><rect x="3" y="6.5" width="6" height="4" fill="#fff" stroke="#999"/></svg>Print This Article</a>
    </div>
  </article>

  <nav class="pager">
    <a href="http://snapgazette.example/gisborne/issue/KLR48_19600714/t1-front-d1.html">Previous article</a><span>|</span>
    <a href="http://snapgazette.example/gisborne/issue/KLR48_19600714/index.html">Issue contents</a><span>|</span>
    <a href="http://snapgazette.example/gisborne/issue/KLR48_19600714/t1-body-d4.html">Next article</a>
  </nav>

  <footer class="site-footer">
    <nav class="footer-links">
      <a href="http://snapgazette.example/gisborne/index.html">Home</a><span>/</span>
      <a href="http://snapgazette.example/gisborne/about.html">About</a><span>/</span>
      <a href="http://snapgazette.example/gisborne/issues/index.html">Browse Gisborne Snap Gazette</a><span>/</span>
      <a href="http://snapgazette.example/gisborne/initial/index.html">A-Z people</a>
    </nav>
    <p class="copyright">Copyright 2014 Snap Gazette.All Right Reserved.</p>
    <div class="licence" aria-hidden="true"></div>
    <div class="social" aria-hidden="true"><span></span><span></span><span></span><span></span></div>
  </footer>
</div>
</body>
</html>
```